Book Cover on Entrepreneurship for Eye Doctors

Book Title: The Lens Practice Builder: How to launch with confidence
Author: Rufus Tembley, Optom, MBA, DBA, EIC
I need a Book Cover with the following descriptions:
Topic: the book topic is entrepreneurship knowledge for eye care professionals.
The book's audience: eye care professionals who you know as Opticians, who sell eyeglasses and sunglasses;
Optometrists, test eyes, fit contact lenses, and prescribe medication
Ophthalmologists, perform eye surgery
More about the audience:
1- Young eye care professionals who don’t know about entrepreneurship and those who are stuck in the 9-to-5 job;
2- This is the first book written on entrepreneurship with eye care professionals in mind.
3- Private practice owners the established business guys who are looking to grow their business;
4- Many eye care professionals are MBA holders they may have learned a little bit about entrepreneurship during their MBA studies.
Use the sample cover above and the suggestions that follow as a guide:
1- The cover should be very simple leaving an empty space somewhere to sign the book;
2- The Title and author name should use a modern font;
3- The cover should provide info about what's inside the book through illustrations, for example:
a- Gears: illustrating entrepreneur growth mindset (or anything more explicit)
b- Spectacles, sunglasses, lenses, eye drops, or any other eye care-related correction tools illustrating eye care (or anything more explicit)
c- Symbols illustrating ideas, opportunity, and profit, like money, charts, light bulbs, brain, and coins,...(or anything more explicit)
d- Entrepreneurship illustrated by Briefcase, tie, suit,... (or anything more explicit)

The rest is your creativity and imagination interplay.

Target Market(s)

Eye care professionals: Opticians, Optometrists, Ophthalmologists, Eye Care Administrators, Students in eye specialties.

Industry/Entity Type

eye care

Requirements
Must have
• 1- The cover should be very simple leaving an empty space somewhere to sign the book; 2- The Title and author name should use a modern font; 3- The cover should provide info about what's inside the book through illustrations, for example: a- Gears: illustrating entrepreneur growth mindset (or anything more explicit) b- Spectacles, sunglasses, lenses, eye drops, or any other eye care-related correction tools illustrating eye care (or anything more explicit) c- Symbols illustrating ideas, opportunity, and profit, like money, charts, light bulbs, brain, and coins,...(or anything more explicit) d- Entrepreneurship illustrated by Briefcase, tie, suit,... (or anything more explicit)

```html
<!DOCTYPE html>
<html lang="en">
<head>
<meta charset="utf-8">
<title>The Lens Practice Builder — Book Cover</title>
<link rel="stylesheet" href="https://fonts.googleapis.com/css2?family=Bebas+Neue&display=swap">
<style>
  :root {
    --backdrop: #d4d4d4;
    --cover-blue: #0da8cc;
    --band-navy: #0b1f3a;
    --title-white: #ffffff;
    --title-cream: #fdf6c4;
    --art-slate: #2d4b67;
  }
  html, body {
    margin: 0;
    padding: 0;
    width: 1199px;
    height: 1200px;
    overflow: hidden;
    background: var(--backdrop);
  }
  .book-cover {
    position: absolute;
    left: 230px;
    top: 40px;
    width: 738px;
    height: 1120px;
    display: block;
  }
  .cover-type {
    font-family: "Bebas Neue", "Oswald", sans-serif;
  }
  .title-main { fill: var(--title-white); }
  .title-accent { fill: var(--title-cream); }
  .rule-white { stroke: var(--title-white); stroke-width: 5; }
  .rule-thin { stroke: var(--title-cream); stroke-width: 1; opacity: 0.8; }
  .author-name { fill: var(--title-white); letter-spacing: 1px; }
</style>
</head>
<body>
<svg class="book-cover" viewBox="0 0 738 1120" xmlns="http://www.w3.org/2000/svg" role="group" aria-label="Book cover: The Lens Practice Builder by Rufus Tembley">
  <rect class="cover-background" x="0" y="0" width="738" height="1120" fill="var(--cover-blue)"/>

  <rect class="trial-frame-art" x="148" y="29" width="442" height="225" rx="40" fill="var(--art-slate)" role="img" aria-label="Illustration of an optometrist's trial lens frame with two round graduated lens holders"/>

  <g class="cover-type">
    <line class="rule-white" x1="120" y1="305" x2="326" y2="305"/>
    <line class="rule-white" x1="410" y1="305" x2="616" y2="305"/>
    <text class="title-main" x="368" y="327" font-size="62" text-anchor="middle">THE</text>

    <text class="title-main" x="120" y="650" font-size="450" textLength="496" lengthAdjust="spacingAndGlyphs">LENS</text>
    <text class="title-main" x="120" y="806" font-size="211" textLength="496" lengthAdjust="spacingAndGlyphs">PRACTICE</text>
    <text class="title-accent" x="120" y="890" font-size="102" textLength="496" lengthAdjust="spacingAndGlyphs">BUILDER</text>

    <line class="rule-thin" x1="162" y1="928" x2="575" y2="928"/>
    <text class="title-main subtitle" x="368" y="965" font-size="33" text-anchor="middle" letter-spacing="1.5">HOW TO LAUNCH WITH CONFIDENCE</text>
    <line class="rule-thin" x1="162" y1="977" x2="575" y2="977"/>

    <rect class="author-band" x="0" y="1020" width="738" height="100" fill="var(--band-navy)"/>
    <text class="author-name" x="68" y="1088" font-size="49" textLength="600" lengthAdjust="spacingAndGlyphs">RUFUS TEMBLEY, OPTOM, MBA, DBA, EIC</text>
  </g>
</svg>
</body>
</html>
```